Business card design for holistic health care clinic

We need a double-sided business card design for our holistic health care clinic that integrates our logo design and also its color scheme. My business is called Valmira. It is an integrative medicine clinic. You have already done the logo for me. Please ensure an elegant and upscale design that is not cluttered, but still has all the necessary information (please see below for details).

Target Market(s)

Wellness, fitness, rehabilitation for educated, well-traveled open-minded clients who are focused on natural, organic, balanced and preventive healthcare and lifestyle.

Industry/Entity Type

Medical

Contact Information for Business Card

Modern, clean.

Number of Pages Required

1 page

Font styles to use
Serif
Sans Serif

Colors

Designer to choose colors to be used in the design.

Requirements
Must have
• Logo on one side, all other information on the other side.
• Other information should include:
• Tobias Wrenfeld - DOE, CPT, LMT
• 4100 East Marrow Drive
• Austin, TX 78119
• 512 555 0148
• 818 555 0192
• info@ValmiraHealth.example
• t.wrenfeld@ValmiraHealth.example
Nice to have
• Darker background on front - but not totally black - shaded/dark gray.

```html
<!DOCTYPE html>
<html lang="en">
<head>
<meta charset="utf-8">
<title>Valmira — Business Card</title>
<link rel="stylesheet" href="https://fonts.googleapis.com/css2?family=Source+Sans+3:wght@400;600&display=swap">
<style>
  :root {
    --page-bg: #e9e7e4;
    --card-bg: #101011;
    --card-edge: #1c1c1e;
    --accent-blue: #1e9ad6;
    --text-light: #e8e8e8;
    --silver: #c9cacc;
    --divider: #3a3a3d;
  }
  * { margin: 0; padding: 0; box-sizing: border-box; }
  html, body {
    width: 1200px; height: 900px; overflow: hidden;
    background: var(--page-bg);
    font-family: "Source Sans 3", "Myriad Pro", sans-serif;
  }
  .sheet {
    width: 1200px; height: 900px;
    display: flex; align-items: center; justify-content: center; gap: 50px;
  }
  .card {
    width: 525px; height: 300px;
    background: var(--card-bg);
    border: 1px solid var(--card-edge);
    position: relative;
    box-shadow: 0 10px 28px rgba(0,0,0,.25);
  }
  /* Back side: brand + contact details */
  .card-back .brand-mark {
    position: absolute; left: 46px; top: 168px;
    display: flex; align-items: center; gap: 10px;
    color: var(--accent-blue);
    font-size: 34px; font-weight: 600;
  }
  .brand-mark .dot {
    width: 14px; height: 14px; border-radius: 50%;
    background: var(--accent-blue);
  }
  .card-back .divider {
    position: absolute; left: 232px; top: 58px;
    width: 1px; height: 186px; background: var(--divider);
  }
  .contact {
    position: absolute; left: 252px; top: 54px;
    color: var(--text-light);
    font-size: 14.5px; line-height: 1.35;
  }
  .contact .person {
    color: var(--accent-blue);
    font-size: 19px; font-weight: 600; margin-bottom: 10px;
  }
  .contact .person .credentials { font-size: 13px; }
  .contact .address { margin-bottom: 14px; }
  .contact ul { list-style: none; }
  .contact li { display: flex; align-items: center; gap: 9px; margin-bottom: 2px; }
  .contact li svg { width: 11px; height: 11px; fill: var(--accent-blue); flex: none; }
  /* Front side: brand name + tagline */
  .card-front { display: flex; align-items: center; justify-content: center; }
  .front-brand { text-align: left; }
  .front-brand .name {
    color: var(--silver);
    font-size: 64px; font-weight: 600; letter-spacing: 1px; line-height: 1;
  }
  .front-brand .tagline {
    color: var(--silver);
    font-size: 18px; font-weight: 400; margin-top: 6px; letter-spacing: .3px;
  }
</style>
</head>
<body>
<main class="sheet">
  <section class="card card-back">
    <div class="brand-mark"><span class="dot"></span>Valmira</div>
    <div class="divider"></div>
    <div class="contact">
      <p class="person">Tobias Wrenfeld <span class="credentials">- DOE, CPT, LMT</span></p>
      <p class="address">4100 East Marrow Drive<br>Austin, TX 78119</p>
      <ul>
        <li><svg viewBox="0 0 12 12"><path d="M2.5 1 4.5 1 5.3 3.6 4 4.6C4.7 6 6 7.3 7.4 8L8.4 6.7 11 7.5 11 9.5C11 10.3 10.3 11 9.5 11 5 11 1 7 1 2.5 1 1.7 1.7 1 2.5 1Z"/></svg>512 555 0148</li>
        <li><svg viewBox="0 0 12 12"><path d="M3 0.5H9V11.5H3ZM4 1.8V9.2H8V1.8ZM5.5 9.8H6.5V10.8H5.5Z" fill-rule="evenodd"/></svg>818 555 0192</li>
        <li><svg viewBox="0 0 12 12"><path d="M0.5 2.5H11.5V9.5H0.5ZM1.5 3.3 6 6.6 10.5 3.3Z" fill-rule="evenodd"/></svg>info@ValmiraHealth.example</li>
        <li><svg viewBox="0 0 12 12"><circle cx="6" cy="6" r="5.5"/></svg>t.wrenfeld@ValmiraHealth.example</li>
      </ul>
    </div>
  </section>
  <section class="card card-front">
    <div class="front-brand">
      <p class="name">Valmira</p>
      <p class="tagline">Integrative Holistic Medicine</p>
    </div>
  </section>
</main>
</body>
</html>
```